New Business Card Design Project

Need a design that will create an impact / strong impression towards our clients for our business. We are in the lighting business and we do lighting retrofits for large commercial to industrial clientele.

Target Market(s)

Lighting Industry

Industry/Entity Type

Business

Font styles to use
Other font styles liked:
• we would like to use the font on our logo, not sure what it is though..

Requirements
Must have
• Our logo.
Nice to have
• We are open to suggestions that have to do with lighting.

```html
<!DOCTYPE html>
<html lang="en">
<head>
<meta charset="utf-8">
<title>Meridian Lightworks Group – Business Card</title>
<link href="https://fonts.googleapis.com/css2?family=Lato:wght@400;700;900&display=swap" rel="stylesheet">
<style>
  :root {
    --bg: #4a4a4a;
    --green-dark: #133f12;
    --green-mid: #0f8a3a;
    --green-light: #5cc55a;
    --white: #ffffff;
    --ink: #111111;
  }
  * { margin: 0; padding: 0; box-sizing: border-box; }
  html, body { width: 1200px; height: 900px; overflow: hidden; }
  body {
    background: var(--bg);
    font-family: "Lato", sans-serif;
    position: relative;
  }
  .card {
    position: absolute;
    left: 250px;
    width: 700px;
    height: 400px;
    overflow: hidden;
  }
  .card--back { top: 30px; background: var(--green-dark); }
  .card--front { top: 470px; background: var(--white); }

  /* back side */
  .back-brand {
    position: absolute;
    top: 140px; left: 0; right: 0;
    display: flex; align-items: center; justify-content: center; gap: 16px;
  }
  .brand-mark { width: 22px; height: 22px; background: var(--green-light); }
  .brand-name {
    font-weight: 900;
    font-size: 38px;
    letter-spacing: 1px;
    color: var(--white);
    line-height: 1.1;
  }
  .brand-sub {
    position: absolute; top: 200px; left: 0; right: 0;
    text-align: center;
    font-size: 15px; letter-spacing: 4px; text-transform: uppercase;
    color: var(--white);
  }
  .back-web {
    position: absolute; bottom: 48px; left: 0; right: 0;
    text-align: center; font-size: 17px; letter-spacing: 1px; color: var(--white);
  }

  /* front side */
  .front-brand {
    position: absolute; top: 34px; left: 44px;
    display: flex; align-items: center; gap: 12px;
  }
  .front-brand .brand-mark { width: 18px; height: 18px; background: var(--green-mid); }
  .front-brand .brand-name { font-size: 30px; color: var(--green-dark); }
  .front-brand-sub {
    position: absolute; top: 78px; left: 44px;
    font-size: 12px; letter-spacing: 3px; text-transform: uppercase; color: var(--green-dark);
  }
  .address {
    position: absolute; top: 118px; left: 44px;
    font-size: 17px; line-height: 1.3; color: var(--ink); font-style: normal;
  }
  .contacts {
    position: absolute; top: 168px; left: 44px;
    list-style: none; font-size: 17px; color: var(--ink);
  }
  .contacts li { display: flex; align-items: center; gap: 10px; height: 26px; }
  .contacts svg { width: 16px; height: 16px; fill: var(--green-mid); }
  .person { position: absolute; top: 208px; left: 450px; }
  .person-name { font-weight: 700; font-size: 26px; color: var(--green-mid); line-height: 1.2; }
  .person-role { font-size: 18px; color: var(--ink); line-height: 1.3; }
  .front-band { position: absolute; left: 0; bottom: 0; width: 700px; height: 100px; }
  .front-web {
    position: absolute; right: 40px; bottom: 14px;
    font-size: 19px; color: var(--white); letter-spacing: .5px;
  }
</style>
</head>
<body>

<section class="card card--back" aria-label="Card back">
  <div class="back-brand">
    <span class="brand-mark"></span>
    <span class="brand-name">Meridian Lightworks</span>
  </div>
  <p class="brand-sub">Group, LLC</p>
  <p class="back-web">www.meridianlight-llc.com</p>
</section>

<section class="card card--front" aria-label="Card front">
  <div class="front-brand">
    <span class="brand-mark"></span>
    <span class="brand-name">Meridian Lightworks</span>
  </div>
  <p class="front-brand-sub">Group, LLC</p>

  <address class="address">
    2418 North Lakeview Avenue<br>Evanston, IL 60201
  </address>

  <ul class="contacts">
    <li>
      <svg viewBox="0 0 24 24" aria-hidden="true"><path d="M6.6 10.8a15 15 0 0 0 6.6 6.6l2.2-2.2c.3-.3.7-.4 1-.2 1.1.4 2.3.6 3.6.6.6 0 1 .4 1 1V20c0 .6-.4 1-1 1A17 17 0 0 1 3 4c0-.6.4-1 1-1h3.5c.6 0 1 .4 1 1 0 1.3.2 2.5.6 3.6.1.3 0 .7-.2 1z"/></svg>
      (555) 014-2200
    </li>
    <li>
      <svg viewBox="0 0 24 24" aria-hidden="true"><path d="M6 2h12v5H6zM3 8h18a1 1 0 0 1 1 1v8h-4v5H6v-5H2V9a1 1 0 0 1 1-1zm5 8v4h8v-4z"/></svg>
      (555) 014-2201
    </li>
    <li>
      <svg viewBox="0 0 24 24" aria-hidden="true"><path d="M2 5h20v14H2zm2 2v.5l8 5.5 8-5.5V7l-8 5.5z"/></svg>
      info@meridianlight-llc.com
    </li>
  </ul>

  <div class="person">
    <p class="person-name">Daniel Reyes</p>
    <p class="person-role">Manager</p>
  </div>

  <svg class="front-band" viewBox="0 0 700 100" preserveAspectRatio="none" aria-hidden="true">
    <path d="M0 0 H700 V100 H0 Z" fill="var(--green-dark)"/>
    <path d="M0 0 H700 V40 C480 42 300 30 0 0 Z" fill="var(--white)"/>
    <path d="M120 12 C320 38 480 44 700 40 V56 C470 58 310 44 120 12 Z" fill="var(--green-mid)"/>
    <path d="M100 10 C320 40 480 48 700 46" stroke="var(--white)" stroke-width="2" fill="none"/>
  </svg>
  <p class="front-web">www.meridianlight-llc.com</p>
</section>

</body>
</html>
```